Diesel injection diagnostics and repairs

I am after a business card design for my business.
The business; repairs diesel fuel systems on 4wds, trucks, earthmoving equipment,can do mobile repairs and diagnostics
The business design can basic but effective, I guess some colours such as green and black or even blue......
The end result should reflect the business name and logo and what the business can do

RW Diesel Injection PTY LTD
rw_diesel@mailbrook.net
Terry Holt
0412836517

```html
<!DOCTYPE html>
<html lang="en">
<head>
<meta charset="UTF-8">
<title>RW Diesel Injection – Business Card</title>
<link rel="stylesheet" href="https://fonts.googleapis.com/css2?family=Anton&family=Oswald:wght@600&family=Tinos:wght@700&display=swap">
<style>
  :root {
    --band-green: #0f4a02;
    --ink: #0a0a0a;
    --echo-grey: #c4c4c4;
    --paper: #ffffff;
    --footer-text: #f2f2ea;
    --spray-light: #f4f4f4;
    --spray-mid: #cfcfcf;
  }
  * { margin: 0; padding: 0; box-sizing: border-box; }
  html, body { width: 741px; height: 1200px; overflow: hidden; background: var(--paper); }
  .card {
    position: relative;
    width: 741px;
    height: 1200px;
    overflow: hidden;
    background: var(--paper);
  }
  .top-band {
    position: absolute; left: 0; top: 0;
    width: 741px; height: 62px;
    background: var(--band-green);
  }
  .injector-photo {
    position: absolute; left: 400px; top: 62px;
    width: 341px; height: 590px;
    background: radial-gradient(ellipse at 72% 38%, var(--spray-mid) 0%, var(--spray-light) 45%, var(--paper) 75%);
  }
  .headline {
    position: absolute; left: 0; top: 400px;
    width: 741px; height: 200px;
  }
  .headline text {
    font-family: "Anton", "Impact", sans-serif;
    font-size: 68px;
  }
  .headline .echo { fill: var(--echo-grey); }
  .headline .main { fill: var(--ink); }
  .service-dot {
    position: absolute;
    width: 44px; height: 44px;
    border-radius: 50%;
    background: var(--paper);
    box-shadow: 0 0 14px 14px rgba(30,30,30,0.85), 0 0 34px 24px rgba(60,60,60,0.35);
  }
  .service-text {
    position: absolute; left: 214px;
    font-family: "Oswald", "Arial Narrow", sans-serif;
    font-weight: 600;
    font-size: 25px;
    letter-spacing: 1px;
    color: var(--ink);
    white-space: nowrap;
  }
  .bottom-band {
    position: absolute; left: 0; top: 1047px;
    width: 741px; height: 153px;
    background: var(--band-green);
    font-family: "Tinos", "Times New Roman", serif;
    font-weight: 700;
    color: var(--footer-text);
  }
  .company-name {
    position: absolute; left: 0; top: 20px; width: 741px;
    text-align: center;
    font-size: 26px;
  }
  .contact {
    position: absolute; top: 67px;
    font-size: 27px;
    white-space: nowrap;
  }
  .contact--email { right: 392px; }
  .contact--phone { left: 380px; }
  .contact-divider {
    position: absolute; left: 364px; top: 76px;
    width: 1px; height: 77px;
    background: var(--footer-text);
  }
</style>
</head>
<body>
<div class="card">
  <div class="top-band"></div>

  <div class="injector-photo" role="img" aria-label="Close-up of a diesel injector nozzle spraying fine fuel jets"></div>

  <svg class="headline" viewBox="0 400 741 200" aria-label="RW Diesel Injection">
    <text class="echo" x="99" y="508" textLength="636" lengthAdjust="spacingAndGlyphs" aria-hidden="true">RW DIESEL INJECTION</text>
    <text class="main" x="99" y="576" textLength="636" lengthAdjust="spacingAndGlyphs">RW DIESEL INJECTION</text>
  </svg>

  <div class="services">
    <span class="service-dot" style="left:110px; top:665px;"></span>
    <p class="service-text" style="top:667px;">Repairs diesel fuel systems on 4wds,</p>
    <p class="service-text" style="top:721px;">trucks &amp; earthmoving equipment</p>

    <span class="service-dot" style="left:110px; top:826px;"></span>
    <p class="service-text" style="top:828px;">Mobile repairs and diagnostics available</p>
  </div>

  <div class="bottom-band">
    <p class="company-name">RW Diesel Injection PTY LTD</p>
    <p class="contact contact--email">rw_diesel@mailbrook.net</p>
    <span class="contact-divider"></span>
    <p class="contact contact--phone">Terry Holt 0412836517</p>
  </div>
</div>
</body>
</html>
```